Banner Ad Designs for tick and flea products

We sell tick and flea products online and want some great banner designs for our online website to promote our tick and flea products.

The ads must be made up in both Flash and HTML5
Ads can be formatted as .JPEG or .GIF files.

Please see the following url for creative requirements
http://help.bannerkite.com/creative-requirements/

Creative licence no limits to your imagination!

Ads must be created in the following sizes:

- Banner – 468×60
- Square – 250×250
- Small Square – 200×200
- Leaderboard – 728×90
- Medium Rectangle – 300×250
- Chatterly – 100×72

please view our website at www.globalpawstore.com.au or .com to get a feel for our website.

The aim is to attract customers who want to save on tick and flea purchases for their pets (dogs and cats)

Target Market(s)

Anyone who owns a dog or cat

Industry/Entity Type

Online

Font styles to use
Sans Serif
Other font styles liked:
• creative licence on font styles

Requirements
Must have
• Must have a strong urge to entice customers to click through.

Images wording and text etc use creative lic
Nice to have
• Strong appeal to dog and cat owners and how they can save on flea and tick essentials.
Keep it simple but effective.
Be fun and playful and inviting.
Should not have
• Please do not use words like cheap - cheapest

Strobing & Flashing - Strobing, flashing backgrounds, or otherwise distracting ads are not allowed. Do not attempt to overtly distract the user from page content.

```html
<!DOCTYPE html>
<html lang="en">
<head>
<meta charset="UTF-8">
<title>Global Paw Store – Tick and Flea Banner Set</title>
<link rel="stylesheet" href="https://fonts.googleapis.com/css2?family=Tenor+Sans&family=Archivo+Narrow:wght@700&display=swap">
<style>
  :root {
    --canvas: #ffffff;
    --leaf: #86ad35;
    --leaf-edge: #9cc24a;
    --leaf-deep: #6f9628;
    --paper: #ffffff;
    --ink-white: #ffffff;
    --ink-label: #111111;
    --ink-brand: #1d2b4a;
    --brand-dot: #2a4f8f;
    --button-top: #8ef05a;
    --button-mid: #3fcf2a;
    --button-bottom: #1f9a16;
    --button-rim: #1b6e12;
    --button-text: #14470f;
    --pets-fur: #b79a78;
    --pets-shadow: #6b5440;
    --pug-fur: #c9a67a;
    --pug-dark: #6a4e33;
  }
  html, body {
    margin: 0;
    padding: 0;
    width: 1200px;
    height: 900px;
    overflow: hidden;
    background: var(--canvas);
  }
  .canvas {
    position: relative;
    width: 1200px;
    height: 900px;
    background: var(--canvas);
  }
  .variant-label {
    position: absolute;
    left: 10px;
    width: 50px;
    font-family: "Tenor Sans", Arial, sans-serif;
    font-size: 48px;
    color: var(--ink-label);
    line-height: 1;
  }
  .banner {
    position: absolute;
    left: 68px;
    width: 1092px;
    height: 135px;
    box-sizing: border-box;
    border: 4px solid var(--leaf-edge);
    background: var(--leaf);
    overflow: hidden;
  }
  .banner--a { top: 192px; }
  .banner--b { top: 364px; }
  .banner--c { top: 536px; }

  .glow {
    position: absolute;
    top: -30px;
    height: 187px;
    width: 300px;
    background: radial-gradient(ellipse 50% 50% at 50% 50%, var(--paper) 82%, rgba(255,255,255,0) 100%);
  }
  .glow--left { left: -40px; }
  .glow--right { right: -40px; width: 340px; }

  .pet-photo {
    position: absolute;
    top: 6px;
    left: 6px;
    width: 176px;
    height: 119px;
    border-radius: 30px 40px 6px 6px;
    background: linear-gradient(100deg, var(--pets-shadow) 0%, var(--pets-fur) 55%, #e6d8c4 100%);
  }
  .pug-photo {
    position: absolute;
    top: 6px;
    right: 10px;
    width: 200px;
    height: 119px;
    border-radius: 40px 20px 4px 4px;
    background: linear-gradient(90deg, var(--pug-dark) 0%, var(--pug-fur) 45%, var(--pug-dark) 100%);
  }

  .headline {
    position: absolute;
    left: 270px;
    width: 550px;
    text-align: center;
    font-family: "Tenor Sans", Arial, sans-serif;
    color: var(--ink-white);
    font-weight: 400;
  }
  .banner--a .headline {
    top: 18px;
    font-size: 40px;
    line-height: 45px;
  }
  .banner--b .headline {
    top: 40px;
    font-size: 40px;
    line-height: 48px;
  }
  .banner--c .headline {
    top: 10px;
    font-size: 38px;
    line-height: 44px;
  }

  .order-button {
    position: absolute;
    left: 446px;
    top: 66px;
    width: 196px;
    height: 51px;
    box-sizing: border-box;
    border: 2px solid var(--button-rim);
    border-radius: 4px;
    background: linear-gradient(180deg, var(--button-top) 0%, var(--button-mid) 50%, var(--button-bottom) 100%);
    font-family: "Archivo Narrow", Arial, sans-serif;
    font-weight: 700;
    font-size: 28px;
    line-height: 47px;
    text-align: center;
    color: var(--button-text);
    letter-spacing: 0.5px;
  }

  .brand {
    position: absolute;
    right: 22px;
    top: 0;
    height: 127px;
    display: flex;
    align-items: center;
    gap: 12px;
    font-family: "Tenor Sans", Arial, sans-serif;
    font-size: 30px;
    line-height: 34px;
    color: var(--ink-brand);
  }
  .brand-dot {
    width: 34px;
    height: 34px;
    border-radius: 50%;
    background: var(--brand-dot);
    flex: none;
  }
  .brand-name {
    width: 160px;
  }
</style>
</head>
<body>
<main class="canvas">

  <div class="variant-label" style="top:213px">A</div>
  <section class="banner banner--a">
    <div class="glow glow--left"></div>
    <div class="glow glow--right"></div>
    <div class="pet-photo" role="img" aria-label="Photo of a small dog and a tabby cat sitting together"></div>
    <p class="headline" style="margin:0">Save on genuine brand<br>tick and flea products</p>
    <div class="brand">
      <span class="brand-dot"></span>
      <span class="brand-name">Global Paw Store</span>
    </div>
  </section>

  <div class="variant-label" style="top:385px">B</div>
  <section class="banner banner--b">
    <div class="glow glow--left"></div>
    <div class="glow glow--right"></div>
    <div class="pet-photo" role="img" aria-label="Photo of a small dog and a tabby cat sitting together"></div>
    <p class="headline" style="margin:0">Protect Your Pets!</p>
    <div class="pug-photo" role="img" aria-label="Photo of three pugs on leashes"></div>
  </section>

  <div class="variant-label" style="top:557px">C</div>
  <section class="banner banner--c">
    <div class="glow glow--left"></div>
    <div class="glow glow--right"></div>
    <div class="pet-photo" role="img" aria-label="Photo of a small dog and a tabby cat sitting together"></div>
    <p class="headline" style="margin:0">Save with us</p>
    <div class="order-button">ORDER NOW</div>
    <div class="brand">
      <span class="brand-dot"></span>
      <span class="brand-name">Global Paw Store</span>
    </div>
  </section>

</main>
</body>
</html>
```